Kelvara Pane Works Business Card

We need a business card design that is suitable for a Glazing Business. We Specialize in Repairing broken windows and doors and are a 24hr on call service. We manufacture Shower screens, Fly screens, Wardrobe doors, Security doors and grilles + mirrors. We stock a variety of mesh including Standard mesh, Pet resistant mesh, Tressmet & Clearweft. We would like to use a combination of Light Blue, Dark Blue, Black & White with perhaps a picture of glass breaking.

Industry/Entity Type

Business

Contact Information for Business Card

Narooma Glass Service60B Glasshouse Rocks RdNarooma NSW 2546PH / FAX - 02 44765210MOB - 0419682350 Andrewemail - kelvarapane@fenmail.example

Font styles to use
Serif

Colors
34a7d8
0255a3
ffffff

Requirements
Must have
• logo with picture of broken or cracked glass

```html
<!DOCTYPE html>
<html lang="en">
<head>
<meta charset="utf-8">
<title>Kelvara Pane Works – Business Card</title>
<link rel="stylesheet" href="https://fonts.googleapis.com/css2?family=Source+Serif+4:wght@400;600&display=swap">
<style>
  :root {
    --backdrop: #151515;
    --card-white: #ffffff;
    --sky: #34a7d8;
    --sky-light: #5ec8e6;
    --deep: #0255a3;
    --ocean: #3a7fc6;
    --ink: #3a3a3a;
  }
  * { box-sizing: border-box; margin: 0; padding: 0; }
  html, body { width: 1200px; height: 900px; overflow: hidden; }
  body {
    background: var(--backdrop);
    font-family: "Source Serif 4", Georgia, serif;
    position: relative;
  }
  .card {
    position: absolute;
    top: 170px;
    width: 347px;
    height: 561px;
    overflow: hidden;
  }
  .card-front { left: 259px; background: var(--card-white); }
  .card-back {
    left: 631px;
    background: linear-gradient(180deg, var(--sky-light) 0%, #4a9ad6 55%, var(--ocean) 100%);
  }
  .tab {
    position: absolute;
    left: 102px;
    width: 143px;
    background: linear-gradient(180deg, var(--sky-light), #3d8fd3);
  }
  .tab-top { top: 0; height: 30px; }
  .tab-bottom { bottom: 0; height: 28px; }

  .brand {
    position: absolute;
    top: 142px;
    left: 0;
    width: 100%;
    display: flex;
    justify-content: center;
    align-items: center;
    gap: 12px;
  }
  .brand-mark {
    width: 50px;
    height: 50px;
    border-radius: 50%;
    background: var(--sky);
    flex: none;
  }
  .brand-name {
    font-weight: 600;
    color: var(--sky);
    text-transform: uppercase;
    line-height: 1;
  }
  .brand-name .line-1 { display: block; font-size: 34px; letter-spacing: 3px; }
  .brand-name .line-2 { display: block; font-size: 17px; letter-spacing: 6.2px; margin-top: 6px; }

  .contact-name {
    position: absolute;
    top: 260px;
    width: 100%;
    text-align: center;
    font-size: 22px;
    font-weight: 600;
    color: var(--sky);
    letter-spacing: 0.5px;
  }
  .contact-list {
    position: absolute;
    top: 308px;
    width: 100%;
    list-style: none;
    font-size: 15px;
    color: var(--ink);
  }
  .contact-list li {
    display: flex;
    justify-content: center;
    align-items: center;
    gap: 8px;
    height: 23px;
  }
  .contact-list svg { width: 12px; height: 12px; fill: var(--sky); flex: none; }
  .address {
    position: absolute;
    top: 415px;
    width: 100%;
    text-align: center;
    font-size: 15px;
    line-height: 23px;
    color: var(--ink);
  }

  .crack-art {
    position: absolute;
    left: -50px;
    top: -70px;
    width: 440px;
    height: 440px;
    border-radius: 50%;
    background: linear-gradient(180deg, rgba(120, 205, 238, 0.55) 0%, rgba(52, 130, 205, 0.55) 100%);
  }
  .services {
    position: absolute;
    top: 397px;
    width: 100%;
    list-style: none;
    text-align: center;
    color: #ffffff;
    font-size: 15px;
    font-weight: 600;
    line-height: 25px;
  }
  .services li::before {
    content: "";
    display: inline-block;
    width: 8px; height: 8px;
    border-radius: 50%;
    background: #ffffff;
    margin-right: 5px;
    vertical-align: 1px;
  }
</style>
</head>
<body>
  <section class="card card-front">
    <div class="tab tab-top"></div>
    <div class="brand">
      <div class="brand-mark" role="img" aria-label="Cracked-glass emblem"></div>
      <h1 class="brand-name"><span class="line-1">Kelvara</span><span class="line-2">Pane Works</span></h1>
    </div>
    <p class="contact-name">MALCOLM</p>
    <ul class="contact-list">
      <li><svg viewBox="0 0 12 12"><path d="M2.5 0.5l2 2.5-1.2 1.3c.6 1.6 1.8 2.8 3.4 3.4L8 6.5l2.5 2-1 2.5C5 11 1 7 1 2.5z"/></svg>02 48931067</li>
      <li><svg viewBox="0 0 12 12"><path d="M3 0h5v3H3zM1 4h10v6H1zM3 10h6v2H3z"/></svg>02 48931067</li>
      <li><svg viewBox="0 0 12 12"><path d="M3 0h6v12H3zM4 1.5v8h4v-8z"/></svg>0419682350</li>
      <li><svg viewBox="0 0 12 12"><path d="M0 2h12v1L6 7 0 3zM0 4.5l6 4 6-4V10H0z"/></svg>kelvarapane@fenmail.example</li>
    </ul>
    <p class="address">17C Tindale Ridge Rd<br>Brindle Bay NSW 2591</p>
    <div class="tab tab-bottom"></div>
  </section>

  <section class="card card-back">
    <div class="crack-art" role="img" aria-label="Large faint cracked-glass emblem"></div>
    <ul class="services">
      <li>Shower screens</li>
      <li>Fly screens</li>
      <li>Wardrobe doors</li>
      <li>Security doors</li>
      <li>Grilles + mirrors</li>
    </ul>
  </section>
</body>
</html>
```